Timber Crest Construction Needs business card

Hey we are in need of business card designs. I have upload our logo as a guideline, but free feel to run with it or come up with something unique.
Pls have fun with it and be creative. the name says it all!
i will give some directions after i see a few entries..
Updates
Logo source file has been uploaded..
Hey because of the logo is so colourful already.
Can we have a few submissions with less colour.
Also we are looking for clever/hidden/descriptive business card.

```html
<!DOCTYPE html>
<html lang="en">
<head>
<meta charset="utf-8">
<title>Timber Crest Construction – Business Cards</title>
<link href="https://fonts.googleapis.com/css2?family=Arimo:wght@400;600&display=swap" rel="stylesheet">
<style>
  :root {
    --backdrop: #e6e3df;
    --card: #ffffff;
    --ink: #2b2b2b;
    --brand-grey: #5b6064;
    --accent-blue: #2f6fb0;
    --rule-blue: #8fc3ea;
    --rule-soft: #dbe9f5;
  }
  * { box-sizing: border-box; margin: 0; padding: 0; }
  html, body {
    width: 1200px; height: 470px; overflow: hidden;
    background: var(--backdrop);
    font-family: "Arimo", Arial, sans-serif;
    color: var(--ink);
  }
  .canvas { position: relative; width: 1200px; height: 470px; }
  .card {
    position: absolute; top: 80px;
    width: 540px; height: 310px;
    background: var(--card);
    box-shadow: 0 6px 18px rgba(0,0,0,.18);
    overflow: hidden;
  }
  .card--front { left: 40px; }
  .card--back { left: 620px; }

  .brand {
    display: flex; align-items: center; gap: 10px;
    color: var(--brand-grey); font-weight: 600;
    letter-spacing: .3px; white-space: nowrap;
  }
  .brand__mark { background: var(--brand-grey); flex: none; }

  .card--front .brand {
    position: absolute; top: 100px; left: 0; right: 0;
    justify-content: center; font-size: 24px;
  }
  .card--front .brand__mark { width: 22px; height: 22px; }

  .holder {
    position: absolute; top: 178px; left: 60px; width: 170px;
    text-align: right;
  }
  .holder__name { color: var(--accent-blue); font-size: 19px; }
  .holder__title { color: var(--accent-blue); font-size: 13px; margin-top: 1px; }
  .holder__address { font-size: 14px; line-height: 1.35; margin-top: 18px; }

  .divider {
    position: absolute; top: 176px; left: 246px;
    width: 2px; height: 106px; background: var(--rule-blue);
  }

  .contact {
    position: absolute; top: 178px; left: 262px;
    list-style: none; font-size: 14px;
  }
  .contact li { display: flex; align-items: center; gap: 6px; height: 21px; }
  .contact svg { width: 13px; height: 13px; flex: none; }

  .card--back .brand {
    position: absolute; top: 96px; left: 48px; right: 30px; font-size: 25px;
  }
  .card--back .brand__mark { width: 24px; height: 24px; }
  .card--back .web {
    position: absolute; top: 146px; left: 100px;
    font-size: 19px; letter-spacing: .3px;
  }
  .band {
    position: absolute; left: 60px; right: 20px; height: 3px;
    background: var(--rule-soft);
  }
  .band--upper { bottom: 40px; }
  .band--lower { bottom: 30px; height: 2px; }
</style>
</head>
<body>
<main class="canvas">

  <section class="card card--front" aria-label="Card front">
    <div class="brand">
      <span class="brand__mark"></span>
      <span class="brand__name">TIMBER CREST CONSTRUCTION</span>
    </div>

    <div class="holder">
      <p class="holder__name">Your Name</p>
      <p class="holder__title">Title</p>
      <p class="holder__address">Street Name City Name<br>State Zipcode</p>
    </div>

    <div class="divider"></div>

    <ul class="contact">
      <li>
        <svg viewBox="0 0 16 16" aria-hidden="true"><circle cx="8" cy="8" r="7.5" fill="none" stroke="#2b2b2b"/><path d="M5.5 4.5l1.5 0 .6 2-1 .8c.5 1.1 1.3 1.9 2.3 2.3l.8-1 2 .6v1.5c-3.5.4-6.8-2.7-6.2-6.2z" fill="#2b2b2b"/></svg>
        0400 555 018
      </li>
      <li>
        <svg viewBox="0 0 16 16" aria-hidden="true"><circle cx="8" cy="8" r="7.5" fill="none" stroke="#2b2b2b"/><path d="M5.5 4.5l1.5 0 .6 2-1 .8c.5 1.1 1.3 1.9 2.3 2.3l.8-1 2 .6v1.5c-3.5.4-6.8-2.7-6.2-6.2z" fill="#2b2b2b"/></svg>
        0400 555 018
      </li>
      <li>
        <svg viewBox="0 0 16 16" aria-hidden="true"><rect x="1" y="4" width="14" height="9" rx="1" fill="#2b2b2b"/><path d="M1.5 4.5L8 9.5l6.5-5" fill="none" stroke="#fff" stroke-width="1.2"/></svg>
        hello@timbercrestbuild.com
      </li>
      <li>
        <svg viewBox="0 0 16 16" aria-hidden="true"><circle cx="8" cy="8" r="7" fill="#2b2b2b"/><path d="M1 8h14M8 1c-3 3.5-3 10.5 0 14M8 1c3 3.5 3 10.5 0 14" fill="none" stroke="#fff" stroke-width=".9"/></svg>
        www.timbercrestbuild.com
      </li>
    </ul>
  </section>

  <section class="card card--back" aria-label="Card back">
    <div class="brand">
      <span class="brand__mark"></span>
      <span class="brand__name">TIMBER CREST CONSTRUCTION</span>
    </div>
    <p class="web">www.timbercrestbuild.com</p>
    <div class="band band--upper"></div>
    <div class="band band--lower"></div>
  </section>

</main>
</body>
</html>
```